Marlow Dermal Studio - Business Banner with Brand Elements

Design:
• We would like to get a creative design for a wide banner that will go outside our medical spa clinic location. We need a designer to make a simple yet colorful and high-quality design layout. We want this banner to be eye-catching and to communicate the services we offer at our business: Laser Hair Removal | Veluxin | Lip Filler.

Requirements:
• We would like the banner to include our companies information which is the following:

Logo
“Refresh Your Skin”
Laser Hair Removal | Veluxin | Lip Filler
(520) 867-2291
www.MarlowDermalStudio.com

Colors:
• Our business colors are orange, a hint of black and white, but mostly peach/orange tones. (Orange: #f78f20 , White: #ffffff)

Fonts:
• Josefins Sans Bold & Lato

Content and images can be located here:
https://files.quibbleshare.com/share/folders/7tKwP3zRa9_LmQxVb2nD5yHc04EeJuFs8?mode=viewing

The following will give you an idea of our brand presentation:
• Our website is: www.MarlowDermalStudio.com
• Our Pictavo; @marlowdermalstudio
• Our Lumora: www.lumoranet.com/marlowdermalstudio

Target Market(s)
• Women 25 - 45

Industry/Entity Type
• Beauty

```html
<!DOCTYPE html>
<html lang="en">
<head>
<meta charset="utf-8">
<title>Marlow Dermal Studio – Refresh Your Skin Banner</title>
<link href="https://fonts.googleapis.com/css2?family=Josefin+Sans:wght@400;600;700&display=swap" rel="stylesheet">
<style>
  :root {
    --backdrop: #333230;
    --orange: #f7a545;
    --orange-deep: #f78f20;
    --charcoal: #3a3a3a;
    --white: #ffffff;
    --skin-light: #e6c9ae;
    --skin-mid: #c89a78;
    --skin-dark: #8a5a3e;
  }
  * { margin: 0; padding: 0; box-sizing: border-box; }
  html, body {
    width: 1200px; height: 1200px; overflow: hidden;
    background: var(--backdrop);
    font-family: "Josefin Sans", sans-serif;
  }
  .banner {
    position: absolute;
    left: 40px; top: 386px;
    width: 1528px; height: 582px;
    transform: scale(0.733);
    transform-origin: top left;
    background: var(--white);
    box-shadow: 6px 8px 14px rgba(0,0,0,0.55);
    overflow: hidden;
  }
  .banner-shapes { position: absolute; inset: 0; width: 1528px; height: 582px; }
  .headline {
    position: absolute; left: 1012px; top: 50px;
    color: var(--white); line-height: 1;
  }
  .headline-line { display: block; font-weight: 600; font-size: 88px; letter-spacing: 2px; }
  .headline-line + .headline-line { margin-top: 4px; }
  .headline-strong { display: block; font-weight: 700; font-size: 178px; letter-spacing: -2px; margin-top: -2px; }
  .service-label {
    position: absolute; color: var(--orange);
    font-weight: 700; font-size: 32px; line-height: 38px; letter-spacing: 0.5px;
    text-transform: uppercase; white-space: nowrap;
  }
  .service-laser { left: 155px; top: 464px; }
  .service-veluxin { left: 492px; top: 485px; }
  .service-filler { left: 800px; top: 488px; }
  .contact {
    position: absolute; color: var(--white);
    font-weight: 600; letter-spacing: 0.5px; white-space: nowrap;
  }
  .contact-phone { left: 1083px; top: 440px; font-size: 32px; }
  .contact-web { left: 1062px; top: 506px; font-size: 30px; }
</style>
</head>
<body>
  <div class="banner">
    <svg class="banner-shapes" viewBox="0 0 1528 582" xmlns="http://www.w3.org/2000/svg">
      <defs>
        <linearGradient id="photoTone" x1="0" y1="0" x2="1" y2="0">
          <stop offset="0" stop-color="var(--skin-light)"/>
          <stop offset="0.45" stop-color="var(--skin-mid)"/>
          <stop offset="0.6" stop-color="var(--skin-dark)"/>
          <stop offset="1" stop-color="var(--skin-light)"/>
        </linearGradient>
      </defs>
      <polygon class="hero-photo" role="img" aria-label="Photo of three women with glowing skin posed cheek to cheek on a beige backdrop"
        points="0,0 935,0 870,408 0,408" fill="url(#photoTone)"/>
      <polygon class="headline-panel" points="952,0 1528,0 1528,378 1067,378 1056,408 885,408" fill="var(--orange)"/>
      <polygon class="contact-panel" points="1067,378 1528,378 1528,582 995,582" fill="var(--charcoal)"/>

      <g class="icon-laser" transform="translate(86,498)">
        <circle r="42" fill="var(--orange)"/>
        <g fill="none" stroke="var(--white)" stroke-width="2.5" stroke-linecap="round" stroke-linejoin="round">
          <path d="M-14,8 L10,-18 L16,-12 L-8,14 Z"/>
          <path d="M10,-18 L14,-22 L20,-16 L16,-12"/>
          <path d="M-8,14 C0,22 8,16 10,22 L14,24"/>
          <rect x="12" y="20" width="7" height="7" rx="1"/>
          <path d="M-20,12 L-28,14 M-20,16 L-26,22 M-16,18 L-18,26"/>
        </g>
      </g>
      <g class="icon-injection" transform="translate(425,503)">
        <circle r="42" fill="var(--orange)"/>
        <g fill="none" stroke="var(--white)" stroke-width="2.5" stroke-linecap="round" stroke-linejoin="round">
          <path d="M-26,-14 L-4,-18 C2,-18 4,-12 0,-10 L6,-8 C10,-6 8,0 4,0 L-6,2 L-24,4"/>
          <path d="M2,-4 L18,20 M6,-6 L22,18 M18,20 L22,18 M20,19 L26,28"/>
          <path d="M6,4 L12,2 M10,10 L16,8"/>
        </g>
      </g>
      <g class="icon-lips" transform="translate(730,500)">
        <circle r="42" fill="var(--orange)"/>
        <g fill="none" stroke="var(--white)" stroke-width="2.5" stroke-linecap="round" stroke-linejoin="round">
          <path d="M-26,-4 C-16,-16 -8,-14 0,-10 C8,-14 16,-16 26,-4 C16,10 -16,10 -26,-4 Z"/>
          <path d="M-26,-4 C-10,0 10,0 26,-4"/>
          <path d="M4,2 L22,26 M8,0 L26,24 M22,26 L26,24"/>
        </g>
      </g>

      <g class="icon-phone" transform="translate(1038,457)">
        <circle r="23" fill="var(--white)"/>
        <circle r="19" fill="none" stroke="var(--orange)" stroke-width="2.5"/>
        <path d="M-6,-10 L-2,-10 L0,-4 L-3,-2 C-1,3 2,6 5,7 L7,4 L12,6 L12,10 C4,12 -10,0 -6,-10 Z" fill="var(--orange)"/>
      </g>
      <g class="icon-web" transform="translate(1017,524)">
        <circle r="23" fill="var(--white)"/>
        <circle r="19" fill="none" stroke="var(--orange)" stroke-width="2.5"/>
        <g fill="none" stroke="var(--orange)" stroke-width="2">
          <circle r="11"/>
          <ellipse rx="5" ry="11"/>
          <path d="M-11,0 H11 M-9,-6 H9 M-9,6 H9"/>
        </g>
      </g>
    </svg>

    <h1 class="headline">
      <span class="headline-line">REFRESH</span>
      <span class="headline-line">YOUR</span>
      <span class="headline-strong">SKIN</span>
    </h1>

    <p class="service-label service-laser">Laser Hair<br>Removal</p>
    <p class="service-label service-veluxin">Veluxin</p>
    <p class="service-label service-filler">Lip Filler</p>

    <p class="contact contact-phone">(520) 867-2291</p>
    <p class="contact contact-web">www.MarlowDermalStudio.com</p>
  </div>
</body>
</html>
```